SkyvornQ Business Cards and Stationary Design

Need a design for our business cards and stationary. I want to carry on the theme of the logo. I want the business cards to have a design on the back. I would like the business cards and the stationary to carry the same theme, design scheme, and branding

Target Market(s)

Airlines and Maintenance Facilities

Industry/Entity Type

Aviation

Contact Information for Business Card

Name
Position Title
Address: 4827 Trellis Hollow Road, Fort Pierce, Florida, 34951
Office Number
Mobile Number
Email
Website

Font styles to use
Serif
Sans Serif

Colors

Designer to choose colors to be used in the design.

```html
<!DOCTYPE html>
<html lang="en">
<head>
<meta charset="utf-8">
<title>SkyvornQ Business Card</title>
<link href="https://fonts.googleapis.com/css2?family=Roboto:wght@400;500;700&display=swap" rel="stylesheet">
<style>
  :root {
    --backdrop: #2e2e2e;
    --card-light: #f3f3f3;
    --navy: #0b2a55;
    --sky: #1aa3e0;
    --body-grey: #555a60;
    --divider: #c4c4c4;
    --white: #ffffff;
  }
  * { margin: 0; padding: 0; box-sizing: border-box; }
  html, body { width: 1200px; height: 960px; overflow: hidden; }
  body {
    position: relative;
    background: var(--backdrop);
    font-family: "Roboto", Arial, sans-serif;
  }
  .card {
    position: absolute;
    width: 600px;
    height: 343px;
    border-radius: 18px;
  }
  .card-front { left: 314px; top: 113px; background: var(--card-light); }
  .card-back { left: 311px; top: 472px; background: var(--navy); }

  .brand {
    position: absolute;
    left: 70px;
    top: 118px;
    width: 224px;
    text-align: center;
  }
  .brand-dot {
    display: block;
    margin: 0 auto 12px;
    width: 72px;
    height: 72px;
    border: 8px solid var(--sky);
    border-radius: 50%;
  }
  .brand-name {
    font-size: 27px;
    font-weight: 700;
    letter-spacing: 2.5px;
    color: var(--navy);
  }
  .divider {
    position: absolute;
    left: 323px;
    top: 82px;
    width: 2px;
    height: 188px;
    background: linear-gradient(to bottom, transparent, var(--divider) 20%, var(--divider) 80%, transparent);
  }
  .details { position: absolute; left: 351px; top: 84px; }
  .person-name { font-size: 22px; font-weight: 700; color: var(--navy); line-height: 26px; }
  .person-title { font-size: 15px; color: var(--sky); line-height: 18px; margin-bottom: 8px; }
  .address { font-size: 14.5px; color: var(--body-grey); line-height: 18px; margin-bottom: 10px; }
  .contact-list { list-style: none; }
  .contact-list li {
    display: flex;
    align-items: center;
    font-size: 14.5px;
    color: var(--body-grey);
    line-height: 19px;
  }
  .contact-list svg { width: 13px; height: 13px; margin-right: 10px; fill: var(--navy); flex: none; }

  .back-mark {
    position: absolute;
    left: 0; right: 0;
    top: 72px;
    text-align: center;
  }
  .back-mark .brand-dot {
    width: 150px; height: 150px;
    border: 14px solid var(--white);
    margin-bottom: 20px;
  }
  .back-mark .brand-name { color: var(--white); font-size: 24px; letter-spacing: 4px; }
  .back-web {
    position: absolute;
    left: 0; right: 0;
    top: 290px;
    text-align: center;
    font-size: 14px;
    letter-spacing: 5.5px;
    color: var(--white);
  }
</style>
</head>
<body>
  <section class="card card-front">
    <div class="brand">
      <span class="brand-dot"></span>
      <div class="brand-name">SKYVORNQ</div>
    </div>
    <div class="divider"></div>
    <div class="details">
      <div class="person-name">DANIEL ROURKE</div>
      <div class="person-title">CEO/FOUNDER</div>
      <div class="address">4827 Trellis Hollow Road<br>Fort Pierce, Florida, 34951</div>
      <ul class="contact-list">
        <li><svg viewBox="0 0 24 24"><path d="M6.6 10.8a15 15 0 0 0 6.6 6.6l2.2-2.2c.3-.3.7-.4 1-.2 1.1.4 2.3.6 3.6.6.6 0 1 .4 1 1V20c0 .6-.4 1-1 1A17 17 0 0 1 3 4c0-.6.4-1 1-1h3.5c.6 0 1 .4 1 1 0 1.3.2 2.5.6 3.6.1.3 0 .7-.2 1z"/></svg>772 415 0391</li>
        <li><svg viewBox="0 0 24 24"><path d="M7 1h10a2 2 0 0 1 2 2v18a2 2 0 0 1-2 2H7a2 2 0 0 1-2-2V3a2 2 0 0 1 2-2zm0 3v14h10V4z"/></svg>772 508 6142</li>
        <li><svg viewBox="0 0 24 24"><path d="M2 5h20v14H2zm2 2v.5l8 5 8-5V7z"/></svg>info@skyvornq.com</li>
        <li><svg viewBox="0 0 24 24"><circle cx="12" cy="12" r="10"/></svg>www.skyvornq.com</li>
      </ul>
    </div>
  </section>

  <section class="card card-back">
    <div class="back-mark">
      <span class="brand-dot"></span>
      <div class="brand-name">SKYVORNQ</div>
    </div>
    <div class="back-web">www.skyvornq.com</div>
  </section>
</body>
</html>
```